4D Cradle Glimpse Luxury Ultrasound Billboard

Design a HIGH-END, MODERN billboard for my private prenatal ultrasound studio, 4D Cradle Glimpse, located in Pace, Florida.
This billboard will be viewed by drivers traveling at highway speeds, so it must be extremely clean, simple, and readable within 6 seconds.
About My Business
4D Cradle Glimpse is a private prenatal ultrasound studio specializing in:
Highest technology 4D/HD Ultrasounds
Early Gender Determination
Pregnancy Confirmation
I have been serving families for nearly 10 years and is known for creating a memorable experience, not just an ultrasound appointment.
Design Style
I DO NOT want:
Flowers
Leaves
Swirls
Glitter
Hearts everywhere
Busy backgrounds
Generic maternity stock graphics
I DO want:
Modern
Luxury
Upscale
Clean
Professional
Eye-catching
Premium medical spa feel
Colors
Use colors from my logo:
LOGO Green ( or a deep green)
Black
White
Soft Gold accents
Images:
Incorporate my professional headshot in a clean, modern way, logo, and the ultrasound images
Text
Keep wording minimal.
Primary Headline ( OPEN TO IDEAS) :
EXAMPLES ( WOULD RATHER SOMETHING MORE CATCHY)
" ADVANCED IMAGING. UNFORGETTABLE MOMENTS"
"MEET YOUR BABY BEFORE BIRTH"
Under headline:
4D Ultrasound • Early Gender • Pregnancy Confirmation
Business Name:
4D Cradle Glimpse
Private Prenatal Ultrasound Studio
Phone Number:
850-471-5923
Important
This billboard must be readable in 5–6 seconds from a moving vehicle.
Less text is better.
The phone number and business name must be visible from a distance.
The design should feel like a premium brand that immediately tells expecting parents:
“This is where I go to see my baby.”
Files Provided
Official logo
Headshot
Ultrasound images
Don’t make this look like a medical office billboard.
Make it look like a luxury baby experience billboard. That’s what separates 4D Cradle Glimpse from hospitals, OB offices, and all the new studios popping up around you. The emotional connection is what gets moms to book. ❤️
Billboard Size - 10.6” x 36”

```html
<!DOCTYPE html>
<html lang="en">
<head>
<meta charset="utf-8">
<title>4D Cradle Glimpse – Billboard Concept</title>
<link rel="stylesheet" href="https://fonts.googleapis.com/css2?family=Montserrat:wght@500;600;700&family=Playfair+Display:wght@700;900&family=Great+Vibes&family=Oswald:wght@600&display=swap">
<style>
  :root{
    --header-green:#4b944e;
    --deep:#070c0b;
    --deep-green:#0b1815;
    --gold:#c9a15a;
    --gold-light:#e9cf8f;
    --gold-dark:#9c7431;
    --white:#ffffff;
    --ink:#0d1412;
    --scrub:#2f4a33;
  }
  *{box-sizing:border-box;margin:0;padding:0}
  html,body{width:1200px;height:848px;overflow:hidden}
  body{
    background:linear-gradient(90deg,#f4f4f4 0%,#e2e2e2 30%,#bcbcbc 60%,#c4c4c4 100%);
    font-family:"Montserrat",sans-serif;position:relative;
  }
  .concept-header{
    position:absolute;left:0;top:0;width:1200px;height:79px;background:var(--header-green);
    color:#f2f2f2;font:500 34px/79px "Montserrat",sans-serif;letter-spacing:2px;text-align:center;
  }
  .billboard{position:absolute;left:82px;width:1035px;height:305px;overflow:hidden;background:var(--deep)}
  .billboard--one{top:148px}
  .billboard--two{top:490px}
  .layer{position:absolute;left:0;top:0}
  .tagline{position:absolute;color:var(--white);font:500 20px/1 "Montserrat",sans-serif;letter-spacing:5px;text-align:center;white-space:nowrap}
  .headline{
    position:absolute;font:900 56px/1 "Playfair Display",serif;white-space:nowrap;
    background:linear-gradient(180deg,var(--gold-light) 0%,var(--gold) 45%,var(--gold-dark) 100%);
    -webkit-background-clip:text;background-clip:text;color:transparent;transform:scaleX(.92);transform-origin:left top;
  }
  .script{position:absolute;color:var(--white);font:400 80px/1 "Great Vibes",cursive;white-space:nowrap}
  .phone{position:absolute;color:var(--ink);font:600 46px/1 "Oswald",sans-serif;white-space:nowrap;transform:scaleX(.9);transform-origin:left top}
  .place{position:absolute;color:var(--ink);font:600 20px/1 "Montserrat",sans-serif;letter-spacing:3.5px;white-space:nowrap}
  .brand-box{
    position:absolute;background:var(--white);border:3px solid var(--gold-light);border-radius:16px;
    display:flex;flex-direction:column;align-items:center;justify-content:center;gap:8px;
  }
  .brand-name{color:var(--gold);font:700 27px/1.05 "Playfair Display",serif;text-align:center}
  .brand-sub{color:var(--scrub);font:600 8.5px/1 "Montserrat",sans-serif;letter-spacing:.8px;border-top:1px solid var(--gold);padding-top:6px}
  .service{position:absolute;text-align:center;color:var(--white);font:700 8.5px/1.25 "Montserrat",sans-serif;letter-spacing:.8px;white-space:nowrap}
  .service-row{position:absolute;display:flex;align-items:center;gap:6px}
  .service-row .item{display:flex;align-items:center;gap:6px;color:var(--white);font:700 8px/1.3 "Montserrat",sans-serif;letter-spacing:.5px;text-align:center;white-space:nowrap}
  .service-row .divider{width:1px;height:28px;background:var(--gold);margin:0 3px}
  .years-badge{position:absolute;text-align:center;color:var(--gold)}
  .years-badge .nearly{font:600 8px/1 "Montserrat",sans-serif;letter-spacing:3px}
  .years-badge .num{font:900 56px/1 "Playfair Display",serif}
  .years-badge .yrs{font:700 12px/1 "Playfair Display",serif;letter-spacing:3px}
  .years-badge .ribbon{font:600 5.5px/1 "Montserrat",sans-serif;letter-spacing:.5px;border:1px solid var(--gold);padding:3px 6px;margin-top:4px}
  .years-badge .note{font:600 4.5px/1.4 "Montserrat",sans-serif;letter-spacing:.5px;margin-top:10px}
</style>
</head>
<body>
  <div class="concept-header">NEW CONCEPT (10.6” X 36”)</div>

  <section class="billboard billboard--one">
    <svg class="layer" width="1035" height="305" viewBox="0 0 1035 305">
      <defs>
        <linearGradient id="goldLine1" x1="0" x2="1"><stop offset="0" stop-color="#9c7431"/><stop offset=".5" stop-color="#e9cf8f"/><stop offset="1" stop-color="#9c7431"/></linearGradient>
      </defs>
      <polygon points="803,0 1035,0 1035,305 717,305" fill="#0b1815"/>
      <polygon points="0,234 737,234 717,305 0,305" fill="#ffffff"/>
      <line x1="150" y1="232" x2="737" y2="232" stroke="#c9a15a" stroke-width="4"/>
      <line x1="803" y1="0" x2="717" y2="305" stroke="url(#goldLine1)" stroke-width="4"/>
      <path d="M260 186 C360 172 460 168 540 172" fill="none" stroke="#c9a15a" stroke-width="3" stroke-linecap="round"/>
      <circle cx="200" cy="268" r="19" fill="#0b1815" stroke="#c9a15a" stroke-width="2"/>
      <path d="M193 259c2-1 4 0 5 2l1 3c0 1 0 2-1 3l-1 1c1 3 3 5 6 6l1-1c1-1 2-1 3-1l3 1c2 1 3 3 2 5l-1 2c-1 1-3 2-5 1c-8-2-14-9-16-17c0-2 1-4 3-5z" fill="#c9a15a"/>
      <g fill="none" stroke="#c9a15a" stroke-width="2">
        <circle cx="808" cy="223" r="26"/><circle cx="892" cy="223" r="26"/><circle cx="976" cy="223" r="26"/>
        <line x1="850" y1="210" x2="850" y2="238" stroke-width="1.5"/><line x1="934" y1="210" x2="934" y2="238" stroke-width="1.5"/>
        <rect x="796" y="210" width="24" height="16" rx="2"/><path d="M792 230h32M802 234h12"/>
        <circle cx="887" cy="222" r="7"/><circle cx="897" cy="222" r="7"/><path d="M887 229v9M883 234h8M902 217l5-5M903 212h4v4"/>
        <path d="M976 236c-12-8-15-13-11-18c3-3 8-2 11 2c3-4 8-5 11-2c4 5 1 10-11 18z"/>
      </g>
    </svg>
    <svg class="layer" width="1035" height="305" viewBox="0 0 1035 305" role="img" aria-label="Ultrasound image of twin babies face to face">
      <defs><linearGradient id="scan1" x1="0" x2="1"><stop offset="0" stop-color="#5a2820"/><stop offset=".35" stop-color="#9a5144"/><stop offset=".5" stop-color="#2a0f0c"/><stop offset=".65" stop-color="#9a5144"/><stop offset="1" stop-color="#6a3027"/></linearGradient></defs>
      <polygon points="568,0 803,0 739,230 503,230" fill="url(#scan1)"/>
      <line x1="568" y1="0" x2="503" y2="230" stroke="#c9a15a" stroke-width="3"/>
    </svg>
    <svg class="layer" width="170" height="305" viewBox="0 0 170 305" role="img" aria-label="Headshot of the studio owner in green scrubs holding an ultrasound probe">
      <defs><linearGradient id="shot1" x1="0" y1="0" x2="0" y2="1"><stop offset="0" stop-color="#2a2520"/><stop offset=".3" stop-color="#b59a74"/><stop offset=".6" stop-color="#2f4a33"/><stop offset="1" stop-color="#22362a"/></linearGradient></defs>
      <path d="M0 0H80C172 60 178 220 146 305H0Z" fill="url(#shot1)"/>
      <path d="M80 0C172 60 178 220 146 305" fill="none" stroke="#c9a15a" stroke-width="3"/>
    </svg>
    <div class="tagline" style="left:225px;top:38px;width:250px">THE FIRST SMILE.</div>
    <div class="headline" style="left:176px;top:68px">THE BIGGEST</div>
    <div class="script" style="left:222px;top:108px">Connection.</div>
    <div class="phone" style="left:232px;top:245px">850-471-5923</div>
    <div class="place" style="left:494px;top:261px">PACE, FLORIDA</div>
    <div class="brand-box" style="left:801px;top:57px;width:208px;height:104px">
      <div class="brand-name">4D Cradle Glimpse</div>
      <div class="brand-sub">PRENATAL ULTRASOUND STUDIO</div>
    </div>
    <div class="service" style="left:773px;top:257px;width:70px">4D<br>ULTRASOUND</div>
    <div class="service" style="left:857px;top:257px;width:70px">EARLY<br>GENDER</div>
    <div class="service" style="left:931px;top:257px;width:90px">PREGNANCY<br>CONFIRMATION</div>
  </section>

  <section class="billboard billboard--two">
    <svg class="layer" width="1035" height="305" viewBox="0 0 1035 305">
      <polygon points="858,0 1035,0 1035,235 791,235" fill="#0b1815"/>
      <rect x="0" y="235" width="1035" height="70" fill="#ffffff"/>
      <line x1="150" y1="233" x2="1035" y2="233" stroke="#c9a15a" stroke-width="4"/>
      <path d="M265 172 C380 156 480 152 570 158" fill="none" stroke="#c9a15a" stroke-width="3" stroke-linecap="round"/>
      <circle cx="219" cy="267" r="20" fill="#0b1815" stroke="#c9a15a" stroke-width="2"/>
      <path d="M212 258c2-1 4 0 5 2l1 3c0 1 0 2-1 3l-1 1c1 3 3 5 6 6l1-1c1-1 2-1 3-1l3 1c2 1 3 3 2 5l-1 2c-1 1-3 2-5 1c-8-2-14-9-16-17c0-2 1-4 3-5z" fill="#c9a15a"/>
    </svg>
    <svg class="layer" width="1035" height="305" viewBox="0 0 1035 305" role="img" aria-label="Ultrasound image of twin babies face to face">
      <defs><linearGradient id="scan2" x1="0" x2="1"><stop offset="0" stop-color="#5a2820"/><stop offset=".35" stop-color="#9a5144"/><stop offset=".5" stop-color="#2a0f0c"/><stop offset=".65" stop-color="#9a5144"/><stop offset="1" stop-color="#6a3027"/></linearGradient></defs>
      <polygon points="623,0 858,0 795,231 559,231" fill="url(#scan2)"/>
      <line x1="623" y1="0" x2="559" y2="231" stroke="#c9a15a" stroke-width="3"/>
    </svg>
    <svg class="layer" width="170" height="305" viewBox="0 0 170 305" role="img" aria-label="Headshot of the studio owner in green scrubs holding an ultrasound probe">
      <defs><linearGradient id="shot2" x1="0" y1="0" x2="0" y2="1"><stop offset="0" stop-color="#2a2520"/><stop offset=".3" stop-color="#b59a74"/><stop offset=".6" stop-color="#2f4a33"/><stop offset="1" stop-color="#22362a"/></linearGradient></defs>
      <path d="M0 0H80C172 60 178 220 146 305H0Z" fill="url(#shot2)"/>
      <path d="M80 0C172 60 178 220 146 305" fill="none" stroke="#c9a15a" stroke-width="3"/>
    </svg>
    <div class="tagline" style="left:238px;top:28px;width:250px">THE FIRST SMILE.</div>
    <div class="headline" style="left:174px;top:48px;font-size:62px">THE BIGGEST</div>
    <div class="script" style="left:224px;top:90px;font-size:84px">Connection.</div>
    <div class="service-row" style="left:203px;top:186px">
      <div class="item">
        <svg width="28" height="28" viewBox="0 0 32 32" fill="none" stroke="#c9a15a" stroke-width="1.8"><rect x="2" y="3" width="28" height="20" rx="1"/><path d="M8 29h16M16 23v6"/></svg>
        <span>4D<br>ULTRASOUND</span>
      </div>
      <div class="divider"></div>
      <div class="item">
        <svg width="26" height="28" viewBox="0 0 30 32" fill="none" stroke="#c9a15a" stroke-width="1.8"><circle cx="12" cy="14" r="8"/><path d="M12 22v9M8 27h8M18 8l7-6M20 2h5v5"/></svg>
        <span>EARLY<br>GENDER</span>
      </div>
      <div class="divider"></div>
      <div class="item">
        <svg width="22" height="22" viewBox="0 0 26 26" fill="none" stroke="#c9a15a" stroke-width="1.8"><circle cx="13" cy="13" r="11"/><path d="M7 13l4 4 9-9"/></svg>
        <span>PREGNANCY<br>CONFIRMATION</span>
      </div>
    </div>
    <div class="phone" style="left:252px;top:240px;font-size:50px">850-471-5923</div>
    <div class="place" style="left:563px;top:262px;font-size:19px;letter-spacing:2.5px">PACE, FLORIDA</div>
    <div class="years-badge" style="left:874px;top:22px;width:130px">
      <div class="nearly">★ NEARLY ★</div>
      <div class="num">10</div>
      <div class="yrs">YEARS</div>
      <div class="ribbon">OF SERVICE &amp; EXPERIENCE</div>
      <div class="note">CREATING MEMORABLE EXPERIENCES<br>FOR FAMILIES SINCE DAY ONE.</div>
    </div>
    <div class="brand-box" style="left:790px;top:178px;width:229px;height:115px">
      <div class="brand-name" style="font-size:29px">4D Cradle Glimpse</div>
      <div class="brand-sub" style="font-size:9px">PRENATAL ULTRASOUND STUDIO</div>
    </div>
  </section>
</body>
</html>
```